Local Roofing/Construction company business needs new biz card design

We need a new business card design, current cards are from the start of this operation and generic at best. We are a local Construction Company (General Contractor) with a majority of our work originating from insurance claims-exterior finish work is the main focus (Roofs-Siding-Gutters etc). Heavily involved with homeowners and the low ball offers they receive from insurance company's after a insurable event takes place. I have attached some of our original logo file(s) below.

```html
<!DOCTYPE html>
<html lang="en">
<head>
<meta charset="utf-8">
<title>Ridgeline Construction – Business Card</title>
<link href="https://fonts.googleapis.com/css2?family=Montserrat:wght@700;800&family=Open+Sans:wght@400;600;700&display=swap" rel="stylesheet">
<style>
  :root {
    --canvas-bg: #e9ebea;
    --card-bg: #061c21;
    --card-bg-deep: #041519;
    --curve-mid: #07222a;
    --curve-dark: #051a1f;
    --accent: #4dbb6b;
    --text-light: #ffffff;
    --back-mark: #0d2a30;
  }
  * { margin: 0; padding: 0; box-sizing: border-box; }
  html, body { width: 1200px; height: 780px; overflow: hidden; }
  body {
    background: var(--canvas-bg);
    font-family: "Open Sans", sans-serif;
    position: relative;
  }
  .card {
    position: absolute;
    top: 60px;
    width: 380px;
    height: 660px;
    border-radius: 26px;
    background: var(--card-bg);
    overflow: hidden;
    box-shadow: 0 10px 28px rgba(0,0,0,0.25);
  }
  .card--back { left: 190px; }
  .card--front { left: 630px; }

  /* Back */
  .back-mark {
    position: absolute;
    left: 50%;
    top: 50%;
    transform: translate(-50%, -50%) rotate(90deg);
    display: flex;
    align-items: center;
    gap: 22px;
    white-space: nowrap;
  }
  .back-mark__square {
    width: 60px; height: 60px;
    background: var(--back-mark);
    border-radius: 6px;
  }
  .back-mark__name {
    font-family: "Montserrat", sans-serif;
    font-weight: 800;
    font-size: 52px;
    letter-spacing: 2px;
    color: var(--back-mark);
    line-height: 1.05;
    text-transform: uppercase;
  }

  /* Front */
  .brand {
    position: absolute;
    top: 44px;
    left: 0; right: 0;
    display: flex;
    justify-content: center;
    align-items: center;
    gap: 12px;
  }
  .brand__square {
    width: 30px; height: 30px;
    background: var(--accent);
    border-radius: 4px;
  }
  .brand__name {
    font-family: "Montserrat", sans-serif;
    font-weight: 800;
    font-size: 22px;
    color: var(--accent);
    letter-spacing: 1px;
    text-transform: uppercase;
  }
  .curves {
    position: absolute;
    left: 0; bottom: 0;
    width: 380px; height: 660px;
  }
  .person {
    position: absolute;
    top: 210px;
    left: 0; right: 0;
    text-align: center;
  }
  .person__name {
    font-family: "Montserrat", sans-serif;
    font-weight: 800;
    font-size: 32px;
    line-height: 1.1;
  }
  .person__first { color: var(--accent); }
  .person__last { color: var(--text-light); }
  .person__title {
    color: var(--text-light);
    font-size: 15px;
    font-weight: 600;
    margin-top: 2px;
  }
  .contact-icons {
    display: flex;
    justify-content: center;
    gap: 8px;
    margin-top: 14px;
  }
  .icon-dot {
    width: 26px; height: 26px;
    border-radius: 50%;
    background: var(--accent);
    display: flex; align-items: center; justify-content: center;
  }
  .contact-list {
    list-style: none;
    margin-top: 12px;
    color: var(--text-light);
    font-size: 15px;
    line-height: 1.5;
  }
  .address {
    position: absolute;
    bottom: 52px;
    left: 0; right: 0;
    text-align: center;
    color: var(--text-light);
    font-size: 15px;
    line-height: 1.45;
  }
  .address .icon-dot { margin: 0 auto 10px; }
</style>
</head>
<body>

  <section class="card card--back" aria-label="Card back">
    <div class="back-mark">
      <span class="back-mark__square"></span>
      <span class="back-mark__name">Ridgeline<br>Construction</span>
    </div>
  </section>

  <section class="card card--front" aria-label="Card front">
    <svg class="curves" viewBox="0 0 380 660" aria-hidden="true">
      <path d="M0 380 Q 60 560 380 530 L380 660 L0 660 Z" fill="var(--curve-mid)"/>
      <path d="M380 360 Q 360 520 150 620 L0 660 L380 660 Z" fill="var(--curve-dark)"/>
      <path d="M60 660 Q 250 590 380 470 L380 660 Z" fill="var(--card-bg-deep)"/>
    </svg>

    <header class="brand">
      <span class="brand__square"></span>
      <span class="brand__name">Ridgeline Construction</span>
    </header>

    <div class="person">
      <h1 class="person__name"><span class="person__first">Elena</span> <span class="person__last">Marsh</span></h1>
      <p class="person__title">Co-Founder</p>

      <div class="contact-icons">
        <span class="icon-dot" aria-label="Phone">
          <svg width="14" height="14" viewBox="0 0 24 24"><path fill="#fff" d="M6.6 10.8a15 15 0 0 0 6.6 6.6l2.2-2.2c.3-.3.7-.4 1-.2 1.1.4 2.3.6 3.6.6.6 0 1 .4 1 1V20c0 .6-.4 1-1 1A17 17 0 0 1 3 4c0-.6.4-1 1-1h3.5c.6 0 1 .4 1 1 0 1.3.2 2.5.6 3.6.1.3 0 .7-.2 1z"/></svg>
        </span>
        <span class="icon-dot" aria-label="Email">
          <svg width="14" height="14" viewBox="0 0 24 24"><path fill="#fff" d="M3 5h18v14H3z"/><path fill="none" stroke="#4dbb6b" stroke-width="2" d="M3 6l9 7 9-7"/></svg>
        </span>
        <span class="icon-dot" aria-label="Website">
          <svg width="14" height="14" viewBox="0 0 24 24"><circle cx="12" cy="12" r="9" fill="none" stroke="#fff" stroke-width="2"/><path d="M3 12h18M12 3c3 3 3 15 0 18M12 3c-3 3-3 15 0 18" fill="none" stroke="#fff" stroke-width="1.6"/></svg>
        </span>
      </div>

      <ul class="contact-list">
        <li>555-210-4837</li>
        <li>555-210-9962 (Emergency)</li>
        <li>www.ridgelinebuilds.com</li>
        <li>office@ridgelinebuilds.com</li>
      </ul>
    </div>

    <address class="address" style="font-style: normal;">
      <span class="icon-dot" aria-label="Location">
        <svg width="14" height="14" viewBox="0 0 24 24"><path fill="#fff" d="M12 2a7 7 0 0 0-7 7c0 5 7 13 7 13s7-8 7-13a7 7 0 0 0-7-7zm0 9.5A2.5 2.5 0 1 1 12 6.5a2.5 2.5 0 0 1 0 5z"/></svg>
      </span>
      42 Cedar Hollow Dr,<br>Fairbrook, MO 63012
    </address>
  </section>

</body>
</html>
```